Willow Cradle Pregnancy and Baby Massage

I need a web design for a new business, WILLOW CRADLE PREGNANCY AND BABY MASSAGE that I am in the process of setting up in the suburbs of Perth, Western Australia. The business is owned and operated by myself and my intention is to service Pregnant Mothers and Parents of Young Babies that would benefit from massage. I would like to have a "Home Page" and pages for "About Me", "Pregnancy Massage", "Baby Massage", a Pricing Page for Pregnancy Massage Sessions, a Pricing Page for Baby Massage Sessions, and a "Contact Me" page to allow clients to either contact me with queries or book available pregnancy massage sessions on a particular day of the week. I would also like a "News" page that would include articles I have written, news about new courses and a link to my Facebook page (yet to be set up). I would like to keep the colour schemes similar to my logo design colours. I need the design to be easy to follow and to appeal to a younger audience (20's to mid 30's).
The target audience is pregnant mothers-to-be wishing to receive massage treatments, and new parents and grandparents of small babies that would like to learn how to massage their babies.
The look and feel should be modern, professional, elegant and feminine.
I need the design to be in a standard format such that I can update the content by myself ( and does not need specialised software) as the company and business progresses.

Target Market(s)

Contact Information for Business Card

Card should have rounded edges. Design should have the same "feel" as the website. Contact Details of my business address, mobile phone, email and website should be included.

Font styles to use
Script

Requirements
Must have
• Same colours as logo design. In cmyk system, the colours are: 20,60,0,0 which best result is pantone 681 and 40,40,0,0 which best result is pantone 2645. Card should include the logo design.

```html
<!DOCTYPE html>
<html lang="en">
<head>
<meta charset="utf-8">
<title>Willow Cradle Pregnancy and Baby Massage</title>
<link href="https://fonts.googleapis.com/css2?family=Open+Sans:wght@400&family=Roboto:wght@400;500&display=swap" rel="stylesheet">
<style>
  :root {
    --orchid: #b866a8;
    --lavender: #8a80bd;
    --ink: #2e2e2e;
    --body-text: #5f5f5f;
    --frame: #cfcfcf;
    --footer-bg: #464646;
    --footer-rule: #8a8a8a;
    --white: #ffffff;
  }
  * { margin: 0; padding: 0; box-sizing: border-box; }
  html, body { width: 823px; height: 1200px; overflow: hidden; background: var(--white); }
  body { position: relative; font-family: "Roboto", Arial, sans-serif; color: var(--ink); }

  .top-stripe { position: absolute; left: 0; top: 0; width: 823px; height: 2px; background: linear-gradient(90deg, var(--orchid), var(--lavender)); }

  .site-header { position: absolute; left: 0; top: 2px; width: 823px; height: 87px; border-bottom: 1px solid #d6d6d6; box-shadow: 0 1px 3px rgba(0,0,0,.12); background: var(--white); }
  .brand { position: absolute; left: 68px; top: 32px; display: flex; align-items: center; gap: 7px; }
  .brand-dot { width: 14px; height: 14px; border-radius: 50%; background: var(--orchid); }
  .brand-name { font-family: "Roboto", Arial, sans-serif; font-weight: 500; font-size: 17px; color: var(--orchid); }
  .join-button { position: absolute; left: 657px; top: 11px; width: 98px; height: 24px; border-radius: 12px; background: var(--orchid); color: var(--white); font-size: 8px; font-weight: 500; display: flex; align-items: center; justify-content: center; }
  .main-nav { position: absolute; top: 54px; left: 0; font-size: 11px; }
  .main-nav a { position: absolute; white-space: nowrap; color: var(--ink); text-decoration: none; }
  .main-nav a.is-current { color: var(--orchid); }

  .hero { position: absolute; left: 0; top: 89px; width: 823px; height: 294px; background: linear-gradient(100deg, #b866a8 0%, #9d76b6 45%, #8a80bd 100%); overflow: hidden; }
  .hero-photo { position: absolute; left: 0; top: 0; }
  .hero-title { position: absolute; left: 68px; top: 78px; font-size: 33px; font-weight: 500; color: var(--white); }
  .hero-subtitle { position: absolute; left: 68px; top: 122px; font-size: 20px; font-weight: 500; color: var(--white); }
  .hero-button { position: absolute; left: 70px; top: 164px; width: 141px; height: 39px; border: 2px solid var(--white); border-radius: 20px; color: var(--white); font-size: 11px; font-weight: 500; display: flex; align-items: center; justify-content: center; }
  .slider-dots { position: absolute; left: 395px; top: 277px; display: flex; gap: 3px; }
  .slider-dots span { width: 9px; height: 9px; border-radius: 50%; border: 1.5px solid var(--white); }
  .slider-dots span.is-active { background: var(--white); }

  .photo-frame { position: absolute; border: 2px solid var(--white); box-shadow: 0 1px 4px rgba(0,0,0,.35); }
  .text-card { position: absolute; width: 380px; height: 183px; border: 1px solid var(--frame); background: var(--white); padding: 0 16px 0 31px; }
  .text-card p { font-family: "Open Sans", Arial, sans-serif; font-size: 12.8px; line-height: 17px; color: var(--body-text); margin-bottom: 7px; }
  .pill-button { width: 104px; height: 34px; border-radius: 17px; background: var(--orchid); color: var(--white); font-size: 11px; font-weight: 500; display: flex; align-items: center; justify-content: center; }

  .intro-photo { left: 69px; top: 403px; width: 374px; height: 222px; background: radial-gradient(ellipse at 40% 55%, #c57d6c 0%, #a88383 45%, #8e6f72 100%); }
  .intro-card { left: 374px; top: 471px; padding-top: 38px; }
  .intro-card .pill-button { margin-top: 11px; }
  .vision-photo { left: 383px; top: 679px; width: 374px; height: 222px; background: radial-gradient(ellipse at 45% 50%, #d7b39c 0%, #8f7563 55%, #c9a586 100%); }
  .vision-card { left: 68px; top: 751px; padding-top: 17px; }
  .vision-card .pill-button { margin-top: 10px; }

  .site-footer { position: absolute; left: 0; top: 966px; width: 823px; height: 234px; background: var(--footer-bg); color: var(--white); }
  .cert-badge { position: absolute; left: 80px; top: 33px; width: 170px; height: 92px; border: 1px solid #bdbdbd; border-radius: 6px; }
  .footer-heading { position: absolute; top: 31px; font-size: 11.5px; font-weight: 500; letter-spacing: .2px; }
  .quick-links { position: absolute; left: 358px; top: 55px; list-style: none; font-family: "Open Sans", Arial, sans-serif; font-size: 8.8px; line-height: 16px; }
  .newsletter { position: absolute; left: 538px; top: 56px; width: 195px; height: 28px; border: 2px solid var(--white); border-radius: 14px; overflow: hidden; display: flex; }
  .newsletter-input { flex: 1; font-family: "Open Sans", Arial, sans-serif; font-size: 8.5px; color: #d0d0d0; padding-left: 20px; display: flex; align-items: center; }
  .newsletter-submit { width: 64px; background: var(--orchid); font-size: 10.5px; font-weight: 500; display: flex; align-items: center; justify-content: center; }
  .footer-rule { position: absolute; left: 69px; top: 184px; width: 685px; height: 1px; background: var(--footer-rule); }
  .copyright { position: absolute; left: 0; top: 199px; width: 812px; text-align: center; font-family: "Open Sans", Arial, sans-serif; font-size: 8.5px; }
</style>
</head>
<body>
  <div class="top-stripe"></div>

  <header class="site-header">
    <div class="brand"><span class="brand-dot"></span><span class="brand-name">Willow Cradle</span></div>
    <div class="join-button">Join With Me Now !</div>
    <nav class="main-nav">
      <a class="is-current" style="left:241px">Home</a>
      <a style="left:296px">About Me</a>
      <a style="left:368px">Pregnancy Massage</a>
      <a style="left:491px">Baby Massage</a>
      <a style="left:588px">Pricing</a>
      <a style="left:648px">News</a>
      <a style="left:700px">Contact Me</a>
    </nav>
  </header>

  <section class="hero">
    <svg class="hero-photo" width="823" height="294" role="img" aria-label="Photo of a mother massaging her baby">
      <defs>
        <linearGradient id="heroPhotoTone" x1="0" y1="0" x2="1" y2="1">
          <stop offset="0" stop-color="#e9e4e3"/>
          <stop offset="0.6" stop-color="#e7b9c6"/>
          <stop offset="1" stop-color="#efe9e8"/>
        </linearGradient>
      </defs>
      <polygon points="550,0 823,0 823,294 444,294" fill="url(#heroPhotoTone)"/>
    </svg>
    <h1 class="hero-title">Willow Cradle</h1>
    <h2 class="hero-subtitle">Pregnancy And Baby Massage</h2>
    <div class="hero-button">Get An Appointment</div>
    <div class="slider-dots"><span class="is-active"></span><span></span><span></span></div>
  </section>

  <div class="photo-frame intro-photo" role="img" aria-label="Photo of two newborns wrapped in a coral blanket"></div>
  <article class="text-card intro-card">
    <p>Willow Cradle Pregnancy and Baby Massage was launched in 2017, offering massage for pregnant women, and instruction of baby massage to parents, grandparents and carers.</p>
    <div class="pill-button">Read More</div>
  </article>

  <div class="photo-frame vision-photo" role="img" aria-label="Photo of two newborns sleeping in a woven basket"></div>
  <article class="text-card vision-card">
    <p>My vision is to provide a professional massage service to pregnant mothers and babies that also benefits from my skills and experience as a midwife.</p>
    <p>My expectation is that after each session, my clients should leave feeling relaxed, calm, emotionally nurtured, soothed and supported.</p>
    <div class="pill-button">Read More</div>
  </article>

  <footer class="site-footer">
    <div class="cert-badge" role="img" aria-label="Certification badge"></div>
    <h3 class="footer-heading" style="left:358px">QUICK LINKS</h3>
    <ul class="quick-links">
      <li>Home</li><li>About Me</li><li>Pregnancy Massage</li><li>Baby Massage</li><li>Pricing</li><li>News</li><li>Contact Me</li>
    </ul>
    <h3 class="footer-heading" style="left:537px">NEWSLETTER SIGNUP</h3>
    <div class="newsletter"><div class="newsletter-input">Email</div><div class="newsletter-submit">Submit</div></div>
    <div class="footer-rule"></div>
    <p class="copyright">Copyright © 2017 Willow Cradle. All Rights Reserved.</p>
  </footer>
</body>
</html>
```